Business card for law firm

Need business card for new law firm. Think confident, authoritative, conservative, but not stuffy or old-fashioned.

Contact Information for Business Card

Content for card - logo (uploaded), plus the following:

Paul Whitcombe (larger font)
Managing Partner (larger font, but not as large as name)
Level 9, 7 Ferris Lane
Sydney NSW 2000
Main Tel 02 9364 2710
Direct Tel 02 8472 3159
Email paul@qvlegal.com.au
www.qvlegal.com.au

Letterhead design should include logo plus:
Level 9, 7 Ferris Lane
Sydney NSW 2000
Tel 02 8472 3159
www.qvlegal.com.au

```html
<!DOCTYPE html>
<html lang="en">
<head>
<meta charset="utf-8">
<title>Quayvale Legal – Business Card</title>
<link href="https://fonts.googleapis.com/css2?family=Cinzel:wght@500;600&family=Jost:wght@400&display=swap" rel="stylesheet">
<style>
  :root {
    --navy: #031b57;
    --paper: #ffffff;
    --backdrop: #e4e4e4;
    --ink-grey: #4a4a4a;
    --title-grey: #6a6a6a;
    --rule: #3a4d8a;
  }
  * { box-sizing: border-box; margin: 0; padding: 0; }
  html, body { width: 1125px; height: 1200px; overflow: hidden; }
  body { background: var(--backdrop); position: relative; font-family: "Jost", sans-serif; }

  .card { position: absolute; left: 150px; width: 826px; height: 471px; }
  .card--front { top: 98px; background: var(--paper); }
  .card--back { top: 631px; background: var(--navy); }

  .brand-front { position: absolute; right: 60px; top: 150px; display: flex; align-items: center; gap: 14px; }
  .brand-front__square { width: 22px; height: 22px; background: var(--navy); }
  .brand-front__name { font-family: "Cinzel", serif; font-weight: 600; font-size: 30px; color: var(--navy); letter-spacing: 1px; }

  .holder { position: absolute; left: 48px; top: 188px; }
  .holder__name { font-family: "Cinzel", serif; font-weight: 600; font-size: 31px; color: var(--navy); line-height: 1; letter-spacing: 0.5px; }
  .holder__title { font-family: "Cinzel", serif; font-weight: 500; font-size: 20px; color: var(--title-grey); line-height: 1.1; letter-spacing: 1px; margin-top: 2px; }

  .address { position: absolute; left: 48px; top: 260px; font-size: 22px; color: var(--ink-grey); line-height: 27px; }

  .contacts { position: absolute; left: 48px; top: 322px; list-style: none; }
  .contacts li { display: flex; align-items: center; height: 27px; font-size: 22px; color: var(--ink-grey); }
  .contacts li.email { font-size: 20px; }
  .contacts svg { width: 20px; height: 20px; margin-right: 16px; fill: var(--navy); }

  .rule { position: absolute; left: 0; right: 0; top: 419px; height: 1px; background: var(--rule); }
  .web { position: absolute; left: 480px; top: 400px; width: 285px; height: 38px; background: var(--navy);
         color: #fff; font-size: 19px; letter-spacing: 4px; display: flex; align-items: center; justify-content: center; }

  .brand-back { position: absolute; left: 0; right: 0; top: 100px; display: flex; flex-direction: column; align-items: center; }
  .brand-back__square { width: 96px; height: 96px; background: var(--paper); }
  .brand-back__name { margin-top: 62px; font-family: "Cinzel", serif; font-weight: 500; font-size: 54px; color: var(--paper); letter-spacing: 2px; }
</style>
</head>
<body>
  <section class="card card--front">
    <div class="brand-front">
      <span class="brand-front__square"></span>
      <span class="brand-front__name">Quayvale</span>
    </div>

    <div class="holder">
      <p class="holder__name">Paul Whitcombe</p>
      <p class="holder__title">Managing Partner</p>
    </div>

    <p class="address">Level 9, 7 Ferris Lane<br>Sydney NSW 2000</p>

    <ul class="contacts">
      <li><svg viewBox="0 0 20 20" aria-hidden="true"><path d="M2 7c0-3 4-4 8-4s8 1 8 4v2h-4V7H6v2H2z"/><path d="M5 10h10l2 8H3z"/><circle cx="10" cy="14" r="2.2" fill="#fff"/></svg>02 9364 2710</li>
      <li><svg viewBox="0 0 20 20" aria-hidden="true"><path d="M5 1h10v18H5zM7 3v12h6V3z"/><circle cx="10" cy="17" r="1" fill="#fff"/></svg>02 8472 3159</li>
      <li class="email"><svg viewBox="0 0 20 20" aria-hidden="true"><path d="M1 6h18v10H1z"/><path d="M1 6l9 6 9-6" fill="none" stroke="#fff" stroke-width="1.5"/></svg>paul@qvlegal.com.au</li>
    </ul>

    <div class="rule"></div>
    <div class="web">www.qvlegal.com.au</div>
  </section>

  <section class="card card--back">
    <div class="brand-back">
      <span class="brand-back__square"></span>
      <span class="brand-back__name">QUAYVALE LEGAL</span>
    </div>
  </section>
</body>
</html>
```